Professional BIO Template with photo and logo

Hello,
I need a professional Bio template developed via Microsoft WORD ASAP!!!!! I would like to just be able to add the text I need to add. So resize-able text boxes. Potentially able to adjust the font. These are the things I need added it to include.
Head shot (attached)
Text Box for Name
Text Box for phone number
Text box for email
KVT Logo (attached)
Maybe a blue banner at the top or some background boxes that are blue or grey. Here are the pantone colors that our company uses.

CORE COLOR
100c 91m 17y 6k 38r 58g 128b Hex #263A80 Pantone 7687 C

CORE CONTRAST COLOR
36c 29m 28y 0k 168r 168g 170b Hex #669999 Pantone Cool Gray 6C

I also attached some examples of what we have been looking at. Instead of green add the blue...instead of black maybe just be white.

Thank you

```html
<!DOCTYPE html>
<html lang="en">
<head>
<meta charset="utf-8">
<title>Grant Ellison – Marketing Manager Bio</title>
<link rel="stylesheet" href="https://fonts.googleapis.com/css2?family=Montserrat:wght@400;500;700&family=Open+Sans:wght@400;600;700&display=swap">
<style>
  :root {
    --core-blue: #263a80;
    --cool-gray: #a8a8aa;
    --panel-gray: #f0f0f2;
    --rule-gray: #c9c9cb;
    --body-text: #5a5a5c;
    --contact-text: #333335;
    --white: #ffffff;
    --backdrop: #e4e4e6;
  }
  * { box-sizing: border-box; margin: 0; padding: 0; }
  html, body { width: 991px; height: 1200px; overflow: hidden; background: var(--backdrop); }
  .bio-sheet {
    position: absolute; left: 94px; top: 37px;
    width: 802px; height: 1125px;
    background: var(--white);
    box-shadow: 0 6px 18px rgba(0,0,0,.18);
    overflow: hidden;
    font-family: "Open Sans", Arial, sans-serif;
  }
  .header-band { position: absolute; left: 0; top: 0; width: 802px; height: 264px; background: var(--core-blue); }
  .content-panel { position: absolute; left: 307px; top: 264px; width: 495px; height: 861px; background: var(--panel-gray); }
  .skyline-decoration {
    position: absolute; left: 0; top: 792px; width: 307px; height: 333px;
    background: linear-gradient(180deg, rgba(240,240,242,0) 0%, var(--panel-gray) 70%);
  }
  .headshot-frame {
    position: absolute; left: 45px; top: 77px; width: 211px; height: 339px;
    background: var(--white); border-radius: 58px 58px 46px 46px;
  }
  .headshot {
    position: absolute; left: 7px; top: 7px; width: 197px; height: 323px;
    border-radius: 50px 50px 38px 38px;
    background: radial-gradient(ellipse at 50% 35%, #6c6c6e 0%, #3e3f42 55%, #1f2433 100%);
  }
  .name {
    position: absolute; left: 337px; top: 86px;
    font-family: "Montserrat", Arial, sans-serif; color: var(--white);
    font-size: 54px; line-height: 60px; letter-spacing: .5px;
  }
  .name-first { font-weight: 700; display: block; }
  .name-last { font-weight: 400; display: block; }
  .name-rule { position: absolute; left: 335px; top: 212px; width: 340px; height: 1.5px; background: var(--white); }
  .job-title {
    position: absolute; left: 335px; top: 220px;
    font-family: "Montserrat", Arial, sans-serif; font-weight: 500;
    color: var(--white); font-size: 18.5px; letter-spacing: 5.6px; line-height: 26px;
  }
  .section-heading { color: var(--core-blue); font-weight: 700; }
  .about { position: absolute; left: 335px; top: 270px; width: 421px; }
  .about .section-heading { font-size: 29px; line-height: 38px; padding-left: 1px; }
  .about-rule { width: 415px; height: 3px; background: var(--rule-gray); margin: 2px 0 9px; }
  .about p {
    font-size: 11.1px; line-height: 17px; color: var(--body-text);
    text-align: justify; margin-bottom: 17px;
  }
  .contact { position: absolute; left: 37px; top: 436px; width: 219px; text-align: center; }
  .contact .section-heading { font-size: 32px; line-height: 36px; }
  .contact-rule { width: 219px; height: 2px; background: var(--rule-gray); margin: 4px 0 6px; }
  .contact-list { list-style: none; color: var(--contact-text); font-size: 14.5px; }
  .contact-list li { line-height: 29px; }
  .company-name {
    position: absolute; left: 59px; top: 680px; width: 159px; text-align: center;
    font-family: "Open Sans", Arial, sans-serif; font-weight: 700;
    font-size: 44px; line-height: 50px; color: var(--core-blue); letter-spacing: 3px;
  }
  .corner-accent-vertical { position: absolute; left: 774px; top: 794px; width: 28px; height: 331px; background: var(--core-blue); }
  .corner-accent-horizontal { position: absolute; left: 470px; top: 1098px; width: 332px; height: 27px; background: var(--core-blue); }
</style>
</head>
<body>
<main class="bio-sheet">
  <div class="header-band"></div>
  <div class="content-panel"></div>
  <div class="skyline-decoration" role="img" aria-label="Faint city skyline decoration"></div>

  <div class="headshot-frame">
    <div class="headshot" role="img" aria-label="Headshot photo of the marketing manager in a dark suit"></div>
  </div>

  <h1 class="name"><span class="name-first">GRANT</span><span class="name-last">ELLISON</span></h1>
  <div class="name-rule"></div>
  <p class="job-title">MARKETING MANAGER</p>

  <section class="contact">
    <h2 class="section-heading">Contact</h2>
    <div class="contact-rule"></div>
    <ul class="contact-list">
      <li>Year, Month/Date</li>
      <li>Your City, Country</li>
      <li>123 - 456 -78</li>
      <li>youremail@domain.com</li>
    </ul>
  </section>

  <div class="company-name">KVT</div>

  <section class="about">
    <h2 class="section-heading">About me</h2>
    <div class="about-rule"></div>
    <p>Lorem ipsum dolor sit amet, consectetuer adipiscing elit, sed diam nonummy nibh euismod tincidunt ut laoreet dolore magna aliquam erat volutpat. Ut wisi enim ad minim veniam, quis nostrud exerci tation ullamcorper suscipit lobortis nisl ut aliquip ex ea commodo consequat. Duis autem vel eum iriure dolor in hendrerit in vulputate velit esse molestie consequat, vel illum dolore eu feugiat nulla facilisis at vero eros et accumsan et iusto odio dignissim qui blandit praesent luptatum zzril delenit augue duis dolore te feugait nulla facilisi.</p>
    <p>Lorem ipsum dolor sit amet, cons ectetuer adipiscing elit, sed diam nonummy nibh euismod tincidunt ut laoreet dolore magna aliquam erat volutpat. Ut wisi enim ad minim veniam, quis nostrud exerci tation ullamcorper suscipit lobortis nisl ut aliquip ex ea commodo consequat. Lorem ipsum dolor sit amet, consectetuer adipiscing elit, sed diam nonummy nibh euismod tincidunt ut laoreet dolore magna aliquam erat volutpat. Ut wisi enim ad minim veniam, quis nostrud exerci tation ullamcorper suscipit lobortis nisl ut aliquip ex ea commodo consequat. Duis autem vel eum iriure dolor in hendrerit in vulputate velit esse molestie consequat, vel illum dolore eu feugiat nulla facilisis at vero eros et accumsan et iusto odio dignissim qui blandit praesent luptatum zzril delenit augue duis dolore te feugait nulla facilisi.</p>
    <p>Lorem ipsum dolor sit amet, cons ectetuer adipiscing elit, sed diam nonummy nibh euismod tincidunt ut laoreet dolore magna aliquam erat volutpat. Ut wisi enim ad minim veniam, quis nostrud exerci tation ullamcorper suscipit lobortis nisl ut aliquip ex ea commodo consequat.</p>
    <p>Lorem ipsum dolor sit amet, consectetuer adipiscing elit, sed diam nonummy nibh euismod tincidunt ut laoreet dolore magna aliquam erat volutpat. Ut wisi enim ad minim veniam, quis nostrud exerci tation ullamcorper suscipit lobortis nisl ut aliquip ex ea commodo consequat. Duis autem vel eum iriure dolor in hendrerit in vulputate velit esse molestie consequat, vel illum dolore eu feugiat nulla facilisis at vero eros et accumsan et iusto odio dignissim qui blandit praesent luptatum zzril delenit augue duis dolore te feugait nulla facilisi.</p>
    <p>Lorem ipsum dolor sit amet, cons ectetuer adipiscing elit, sed diam nonummy nibh euismod tincidunt ut laoreet dolore magna aliquam erat volutpat. Ut wisi enim ad minim veniam, quis nostrud exerci tation ullamcorper suscipit lobortis nisl ut aliquip ex ea commodo consequat. Lorem ipsum dolor sit amet, consectetuer adipiscing elit, sed diam nonummy nibh euismod tincidunt ut laoreet dolore magna aliquam erat volutpat. Ut wisi enim ad minim veniam, quis nostrud exerci tation ullamcorper suscipit lobortis nisl ut aliquip ex ea commodo consequat. Duis autem vel eum iriure dolor in hendrerit in vulputate velit esse molestie consequat, elit, sed diam nonummy nibh euismod.</p>
  </section>

  <div class="corner-accent-vertical"></div>
  <div class="corner-accent-horizontal"></div>
</main>
</body>
</html>
```